QLR Newsletter

QLR provides mortgage processing outsource services to Mortgage Lenders in Australia and New Zealand. The company employs approximately 300 staff based in offices in Sydney, Melbourne, Brisbane, Adelaide and Perth in Australia and Auckland, New Zealand.
The company acquired a similar and much larger business in 2012 which is being integrated into the one business.
The objectives of a newsletter are to:
- Support the development of the company culture
- Develp a sense of "one team"
- Provide a communication forum for management and staff
I am seeking design options for the newsletter. We will develop/include specific content which will likley evolve over time.
A copy of the company brand gudelines and logo is attached for reference. Our website is currently going through a redesign. Additional information can be provided on request.
Updates

Target Market(s)

The target market for the newsletter is staff. This is a diverse group in terms of locations, age, gender, occupations etc.

Industry/Entity Type

Communication

Requirements
Must have
• Information to be included in the newsletter should include:
- Business results (activity, volumes, performance to budget)
- Client news section (recent developments, client profiling etc)
- New initiatives (update on key projects and new business initiatives, initiatives roadmap)
- Office news (news section for each office including new employees, team profile of the month, report on social events)
- CEO report

```html
<!DOCTYPE html>
<html lang="en">
<head>
<meta charset="utf-8">
<title>QLR Newsletter</title>
<link rel="stylesheet" href="https://fonts.googleapis.com/css2?family=Carlito:wght@400;700&family=Arimo&display=swap">
<style>
  :root {
    --navy: #1b2a6b;
    --deep-blue: #1f5fa8;
    --mid-blue: #3f8fcf;
    --pale-blue: #d6ebf8;
    --heading-blue: #1d5a9a;
    --ink: #2d2d2d;
    --paper: #ffffff;
    --backdrop: #e9ebee;
  }
  * { margin: 0; padding: 0; box-sizing: border-box; }
  html, body { width: 1200px; height: 849px; overflow: hidden; }
  body { background: var(--backdrop); font-family: "Carlito", sans-serif; color: var(--ink); position: relative; }

  .page { position: absolute; top: 89px; width: 462px; height: 668px; background: var(--paper); overflow: hidden; }
  .page--intro { left: 73px; }
  .page--brand { left: 660px; }

  .masthead { position: absolute; left: 0; top: 0; width: 100%; height: 99px;
    background: linear-gradient(90deg, #f4f9fd 0%, var(--pale-blue) 35%, var(--mid-blue) 75%, var(--deep-blue) 100%); }
  .masthead__rule { position: absolute; left: 0; top: 99px; width: 100%; height: 16px;
    background: linear-gradient(90deg, #6fb3e0 0%, var(--deep-blue) 55%, var(--navy) 100%); }
  .masthead__section { position: absolute; left: 186px; top: 67px; font-size: 15px; letter-spacing: .5px; color: #222; }
  .brand-name { position: absolute; left: 318px; top: 8px; font-size: 64px; font-weight: 700; color: var(--navy); letter-spacing: 1px; line-height: 1; }

  .edge-marks { position: absolute; left: 2px; top: 124px; width: 22px; height: 520px;
    background: repeating-linear-gradient(to bottom, transparent 0 4px, var(--deep-blue) 4px 16px, transparent 16px 23.4px); }
  .edge-marks::after { content: ""; position: absolute; inset: 0;
    background: repeating-linear-gradient(to bottom, transparent 0 6px, rgba(255,255,255,.35) 6px 9px, transparent 9px 23.4px); }

  .footer-rule { position: absolute; left: 0; bottom: 0; width: 100%; height: 17px;
    background: linear-gradient(90deg, var(--navy) 0%, var(--deep-blue) 40%, #8fc6ea 100%); }

  .photo { position: absolute; }
  .photo--banner { left: 26px; top: 124px; width: 436px; height: 110px;
    background: linear-gradient(90deg, #c9dff2 0%, #e8f1f9 45%, #8a7a66 78%, #5b4d3f 100%); }
  .banner-title { position: absolute; left: 30px; top: 170px; font-family: "Arimo", sans-serif; font-size: 14px; color: #333; }
  .photo--villa-a { left: 42px; top: 531px; width: 158px; height: 109px; background: linear-gradient(180deg, #6fa7d8 0%, #e6eef2 55%, #4f8a3c 100%); }
  .photo--villa-b { left: 200px; top: 531px; width: 117px; height: 109px; background: linear-gradient(180deg, #2b4a7c 0%, #d9dcd8 55%, #3e3b30 100%); }

  .photo-strip { position: absolute; left: 21px; top: 149px; width: 437px; height: 108px; border-radius: 8px; overflow: hidden; display: flex; }
  .photo-strip .photo { position: static; height: 100%; }
  .photo--house-a { width: 137px; background: linear-gradient(180deg, #8fb6d6 0%, #e8ecee 55%, #4f6b3a 100%); }
  .photo--house-b { width: 154px; background: linear-gradient(180deg, #7fb2dc 0%, #c7d7df 45%, #2f7fb5 100%); }
  .photo--house-c { width: 146px; background: linear-gradient(180deg, #4d8fcf 0%, #eef0ec 55%, #2e77a8 100%); }
  .strip-fade { position: absolute; left: 21px; top: 257px; width: 437px; height: 30px;
    background: linear-gradient(180deg, rgba(120,160,190,.25), rgba(255,255,255,0)); }

  .copy { position: absolute; left: 50px; width: 400px; font-size: 8.6px; line-height: 17px; }
  .page--brand .copy { left: 46px; width: 380px; }
  .copy h2 { font-size: 9px; font-weight: 700; color: var(--heading-blue); text-transform: uppercase; margin-bottom: 2px; letter-spacing: .2px; }
  .copy p + h2, .copy ul + h2 { margin-top: 17px; }
  .copy p + p { margin-top: 0; }
  .copy .gap { margin-top: 11px; }
  .copy ul { list-style: none; }
  .copy li { position: relative; padding-left: 15px; }
  .copy li::before { content: ""; position: absolute; left: 3px; top: 7px; width: 3px; height: 3px; background: var(--ink); }

  .page-title { position: absolute; left: 0; top: 123px; width: 100%; text-align: center; font-size: 11.5px; letter-spacing: .3px; color: #222; }
</style>
</head>
<body>

<section class="page page--intro">
  <header class="masthead"></header>
  <div class="masthead__rule"></div>
  <div class="masthead__section">INTRODUCTION</div>
  <div class="brand-name">QLR</div>
  <div class="edge-marks"></div>

  <div class="photo photo--banner" role="img" aria-label="Photo of a house roof against a cloudy blue sky"></div>
  <div class="banner-title">Smarter Mortgage Solutions Newsletter</div>

  <article class="copy" style="top:247px">
    <h2>Brand Vision Statement – Internal Message</h2>
    <p>The acquisition of Harbourline Lending Services Ltd in August 2012 reflects QLR’s commitment to become the most recognised and reputable leader in its industry. Our focus is to continue to develop and deliver value added, client centric solutions and services. The QLR team is committed to delivering a superior customer experience that encourages innovative thinking and fosters collaborative client relationships.</p>
    <h2>The Purpose of the Brand Graphic Identity Standards</h2>
    <p>A brand is a set of perceptions and images that represent a company, product or service. Whilst many people refer to brand as a logo, tagline, audio jingle etc., a brand is actually much larger. Brand is really the essence or promise of what will be delivered or experienced.</p>
    <p>Accordingly brands are generally developed over time and the most important element of establishing a brand becomes the real-life experiences of clients and customers utilising a product or service.</p>
    <p>The establishment, deployment and consistent application of the brand standards, in all communications, is a key step in realising the vision statement above and in QLR successfully establishing its unique brand. Any queries regarding the application of the brand standards should be referred to the CEO.</p>
  </article>

  <div class="photo photo--villa-a" role="img" aria-label="Photo of a white modern villa with a pool and palm trees"></div>
  <div class="photo photo--villa-b" role="img" aria-label="Photo of a white modern house at dusk"></div>

  <footer class="footer-rule"></footer>
</section>

<section class="page page--brand">
  <header class="masthead"></header>
  <div class="masthead__rule"></div>
  <div class="brand-name">QLR</div>
  <div class="edge-marks"></div>

  <h1 class="page-title">OUR NAME AND BRAND IDENTIFIER</h1>

  <div class="photo-strip">
    <div class="photo photo--house-a" role="img" aria-label="Photo of a modern white house with a garden"></div>
    <div class="photo photo--house-b" role="img" aria-label="Photo of a glass house with a pool by the sea"></div>
    <div class="photo photo--house-c" role="img" aria-label="Photo of a modern house with palm trees and a pool"></div>
  </div>
  <div class="strip-fade"></div>

  <article class="copy" style="top:275px">
    <h2>Our Name</h2>
    <p class="gap">The QLR Group comprises Quayline Loan Resources Ltd, Quayline Loan Resources Pty Ltd and Quayline Loan Resources Australia Pty Ltd.</p>
    <p class="gap">Whilst the full relevant company name needs to be referred to on all legal documents etc QLR is the name we wish to be known by. For example when talking to clients, customers and suppliers we should refer to ourselves as XXX YYY from QLR.</p>
    <h2>About Our Brand Identifier</h2>
    <p class="gap">QLR’s Brand identifier, or “logo” is comprised of a “globe” symbol and the word QLR. We also refer to the combination of our symbol and name as our “brand signature”.</p>
    <p class="gap">The fusion of imagery, typography and colour evoke the primary characteristics of QLR itself.</p>
    <ul>
      <li>The globe represents our global presence and reach.</li>
      <li>The dominate QLR serves to create a memorable stamp and an easily recognisable presence.</li>
      <li>The rich blue hues in the globe not only match the primary dark blue in the Northgate parent logo but also provide a strong pallete that works across all platforms.</li>
      <li>Our logo is professional and strong, yet friendly.</li>
    </ul>
  </article>

  <footer class="footer-rule"></footer>
</section>

</body>
</html>
```